KRV Business Card

Looking for a business card for my restaurant group I own. Four different concepts:

Copperfield Alehouse
Bristow Alehouse
Tanager's Stone Hearth Kitchen
Pellston Patty Company

Card doesn't need to include all the logos.

```html
<!DOCTYPE html>
<html lang="en">
<head>
<meta charset="utf-8">
<title>KRV Business Card</title>
<link rel="stylesheet" href="https://fonts.googleapis.com/css2?family=Poppins:wght@400;600&display=swap">
<style>
  :root {
    --backdrop: #231f20;
    --gold: #d1b06d;
    --slate: #74757a;
    --white: #ffffff;
    --ink-grey: #5f6065;
  }
  * { margin: 0; padding: 0; box-sizing: border-box; }
  html, body {
    width: 1125px;
    height: 1200px;
    overflow: hidden;
    background: var(--backdrop);
    font-family: "Poppins", Arial, sans-serif;
  }
  .canvas { position: relative; width: 1125px; height: 1200px; }

  .card {
    position: absolute;
    left: 171px;
    width: 826px;
    height: 471px;
    overflow: hidden;
  }
  .card--front { top: 106px; background: var(--white); }
  .card--back { top: 639px; background: var(--slate); }

  .contact-panel {
    position: absolute;
    left: 0; top: 0;
    width: 378px; height: 100%;
    background: var(--gold);
    color: var(--white);
    padding: 88px 0 0 37px;
  }
  .contact-panel__name { font-size: 31px; font-weight: 600; line-height: 1.1; }
  .contact-panel__title { font-size: 20px; font-weight: 400; line-height: 1.2; margin-bottom: 24px; }
  .contact-panel__address,
  .contact-panel__lines { font-size: 19.5px; font-weight: 400; line-height: 26px; font-style: normal; list-style: none; }
  .contact-panel__address { margin-bottom: 10px; }

  .edge-strip {
    position: absolute;
    right: 0; top: 0;
    width: 22px; height: 100%;
    background: var(--slate);
  }

  .brand-block {
    position: absolute;
    left: 378px; right: 22px; top: 0; bottom: 0;
    display: flex;
    flex-direction: column;
    align-items: center;
    justify-content: center;
    gap: 6px;
    color: var(--gold);
    font-weight: 600;
  }
  .brand-block__initials { font-size: 72px; line-height: 1; letter-spacing: 4px; }
  .brand-block__name { font-size: 30px; line-height: 1.1; letter-spacing: 3px; text-transform: uppercase; }

  .back-mark {
    position: absolute;
    left: 0; right: 0; top: 115px;
    text-align: center;
    color: var(--white);
    font-size: 180px;
    font-weight: 600;
    line-height: 1;
    letter-spacing: 8px;
  }
  .back-url {
    position: absolute;
    left: 0; right: 0; top: 388px;
    text-align: center;
    color: var(--white);
    font-size: 19px;
    letter-spacing: 4.5px;
    text-transform: uppercase;
  }
</style>
</head>
<body>
<main class="canvas">
  <section class="card card--front" aria-label="Card front">
    <div class="contact-panel">
      <h1 class="contact-panel__name">Daniel Hartley</h1>
      <p class="contact-panel__title">President</p>
      <address class="contact-panel__address">4120 Larkspur Way<br>Juneau, Alaska 99801</address>
      <ul class="contact-panel__lines">
        <li>555-214-7730</li>
        <li>555-386-1092</li>
        <li>555-473-2648</li>
        <li>name@kestrelridgevenues.com</li>
        <li>www.kestrelridgevenues.com</li>
      </ul>
    </div>
    <div class="brand-block">
      <span class="brand-block__initials">KRV</span>
      <span class="brand-block__name">Kestrel Ridge Venues</span>
    </div>
    <div class="edge-strip"></div>
  </section>

  <section class="card card--back" aria-label="Card back">
    <div class="back-mark">KRV</div>
    <p class="back-url">www.kestrelridgevenues.com</p>
  </section>
</main>
</body>
</html>
```